Business card design for Brivo Engineering Tandem

We need a new business card design along with all the necessary to place an order. The company is Brivo Engineering Tandem and we recently updated our logo.

```html
<!DOCTYPE html>
<html lang="en">
<head>
<meta charset="utf-8">
<title>Brivo Engineering Tandem – Business Card</title>
<link rel="stylesheet" href="https://fonts.googleapis.com/css2?family=Kanit:wght@400;600&display=swap">
<style>
  :root {
    --backdrop: #3b3b3d;
    --card: #1e1e1f;
    --accent: #e2c02a;
    --ink: #f2f2f2;
    --mark-grey: #9c9c9c;
    --shadow: rgba(0,0,0,0.55);
  }
  * { margin: 0; padding: 0; box-sizing: border-box; }
  html, body { width: 1200px; height: 1059px; overflow: hidden; }
  body {
    background: var(--backdrop);
    font-family: "Kanit", sans-serif;
    position: relative;
  }
  .card {
    position: absolute;
    left: 256px;
    width: 688px;
    height: 392px;
    background: var(--card);
    border-radius: 24px;
    box-shadow: 0 10px 24px var(--shadow);
  }
  .card--front { top: 100px; }
  .card--back { top: 536px; }

  .brand {
    position: absolute;
    display: flex;
    align-items: center;
    gap: 10px;
  }
  .brand__square {
    width: 14px; height: 14px;
    background: var(--accent);
    flex: none;
  }
  .brand__name {
    color: var(--mark-grey);
    font-weight: 600;
    white-space: nowrap;
  }
  .card--front .brand {
    left: 32px; top: 183px;
    width: 290px;
  }
  .card--front .brand__name { font-size: 20px; line-height: 28px; }

  .card--back .brand {
    left: 0; right: 0; top: 170px;
    justify-content: center;
  }
  .card--back .brand__square { width: 22px; height: 22px; }
  .card--back .brand__name { font-size: 40px; line-height: 52px; }

  .divider {
    position: absolute;
    left: 340px; top: 82px;
    width: 2px; height: 228px;
    background: var(--accent);
  }
  .details {
    position: absolute;
    left: 357px; top: 74px;
    color: var(--ink);
  }
  .details__name {
    color: var(--accent);
    font-weight: 600;
    font-size: 32px;
    line-height: 40px;
    letter-spacing: 0.2px;
  }
  .details__role { font-size: 17px; line-height: 22px; }
  .details__company { font-size: 17px; line-height: 27px; margin-top: 26px; }
  .contacts { list-style: none; margin-top: 18px; }
  .contacts li {
    display: flex;
    align-items: center;
    gap: 8px;
    font-size: 17px;
    line-height: 27px;
  }
  .contacts svg { width: 15px; height: 15px; fill: var(--accent); flex: none; }
</style>
</head>
<body>
  <section class="card card--front">
    <div class="brand">
      <span class="brand__square"></span>
      <span class="brand__name">Brivo Engineering Tandem</span>
    </div>
    <div class="divider"></div>
    <div class="details">
      <p class="details__name">DANIEL HALE</p>
      <p class="details__role">Managing Director</p>
      <p class="details__company">Brivo Engineering Tandem<br>22b Marlow Court, Kettering NN15 6XR</p>
      <ul class="contacts">
        <li>
          <svg viewBox="0 0 16 16" aria-hidden="true"><path d="M1 6c0-2 3-3 7-3s7 1 7 3v1h-3.5V5.5h-7V7H1z M3.5 8h9l1.5 5H2z"/></svg>
          01536 482907
        </li>
        <li>
          <svg viewBox="0 0 16 16" aria-hidden="true"><path d="M1 3h14v1.5L8 9 1 4.5z M1 6.3 8 10.8l7-4.5V13H1z"/></svg>
          sales@brivoengineering.co.uk
        </li>
        <li>
          <svg viewBox="0 0 16 16" aria-hidden="true"><circle cx="8" cy="8" r="7"/><path d="M5 4c2 0 2 2 3 3s-1 2-2 3-1 3-1 3M11 5c-1 1 0 2 1 3" stroke="#1e1e1f" stroke-width="1.4" fill="none"/></svg>
          www.brivoengineering.co.uk
        </li>
      </ul>
    </div>
  </section>

  <section class="card card--back">
    <div class="brand">
      <span class="brand__square"></span>
      <span class="brand__name">Brivo Engineering Tandem</span>
    </div>
  </section>
</body>
</html>
```